Brochure for a civil enineering company in A4 format

I need a brochure design for our company TIRO Engineering S.r.l.. We are an engineering consultant company. Our main clients are from the infrastructure industry (geotechnical and underground sectors mainly).
We are looking for a 2 pages (4 faces) fold out design with a glued pocket where we can put individual data sheets.
I need A4 format pages.

Target Market(s)

We are an engineering consultant company. Our main clients are from the infrastructure industry (geotechnical and underground sectors mainly).

Industry/Entity Type

Civil Engineer

Font styles to use
Sans Serif

Requirements
Must have
• Overall: 2 pages in A4 format
Essential style. Bright and modern appearance.
Glued pocket
Logo integrated in a picture on the pocket where I would like to insert a slogan (… tiro engineering … reliable solutions …)
Attached are selected images which the designer can use and edit at their own discretion.
Some advice in the following (anyway designers are free to provide their solutions):
Outer sheets:
Front page with name, logo. It could be nice to have the “m” of the logo integrated in a pictures, also a modified picture (I mean modify one of the attached pictures) so to create a general image and do not tie the cover to a specific job.
Back page: offices address and contact email address. Nice to have one space for a slogan.
Inner sheet: text that I upload in the file “inside-sheets”, possibly with pictures on each sheet. In the right faces insert the glued pocket. On this pages insert the section OUR EXPERIENCE ….with a space for a picture of our team.
Nice to have
• Clean and essential design.
Pictures choosing from the atteched ones. Pictures could be modified in a very light manner to make them a general idea of the work ( I mean geotechnical world) without to be immediately linked to a specific site.
Should not have
• excessive frills

```html
<!DOCTYPE html>
<html lang="it">
<head>
<meta charset="utf-8">
<title>TIRO Engineering – Brochure</title>
<link rel="stylesheet" href="https://fonts.googleapis.com/css2?family=Montserrat:wght@300;400;500;600;700&family=Roboto+Slab:wght@400&display=swap">
<style>
  :root {
    --backdrop: #e6e6e6;
    --paper: #f7f7f7;
    --paper-shade: #e4e4e4;
    --ink: #2b2b2b;
    --ink-soft: #555555;
    --rule: #4a4a4a;
    --tint-light: #dadada;
    --tint-mid: #c9c9c9;
    --black: #1c1c1c;
  }
  * { box-sizing: border-box; margin: 0; padding: 0; }
  html, body { width: 1148px; height: 1200px; overflow: hidden; }
  body {
    background: var(--backdrop);
    font-family: "Montserrat", sans-serif;
    color: var(--ink);
    position: relative;
  }
  .spread {
    position: absolute;
    left: 85px;
    width: 977px;
    height: 460px;
    background: var(--paper);
    overflow: hidden;
    box-shadow: 0 14px 18px -10px rgba(0,0,0,0.25);
  }
  .spread--outer { top: 100px; }
  .spread--inner { top: 647px; }
  .spread > * { position: absolute; }

  .panel-tint { top: 0; height: 100%; }
  .panel-tint--dotted {
    background:
      linear-gradient(180deg, rgba(210,210,210,0.55) 0%, rgba(230,230,230,0.25) 35%, rgba(247,247,247,0) 60%),
      linear-gradient(135deg, #ededed 0%, #f4f4f4 45%, #e8e8e8 70%, #f3f3f3 100%);
  }
  .panel-tint--cover { background: linear-gradient(160deg, #efefef 0%, #f9f9f9 40%, #f2f2f2 100%); }
  .panel-tint--inner-left { background: linear-gradient(170deg, #ececec 0%, #f3f3f3 50%, #e9e9e9 100%); }
  .panel-tint--inner-mid { background: linear-gradient(190deg, #f1f1f1 0%, #f8f8f8 55%, #efefef 100%); }
  .panel-tint--inner-right { background: linear-gradient(160deg, #f9f9f9 0%, #f1f1f1 100%); }
  .fold { top: 0; width: 1px; height: 100%; background: rgba(0,0,0,0.07); }

  .section-title {
    font-size: 13px;
    font-weight: 300;
    letter-spacing: 0.3px;
    color: var(--ink);
    white-space: nowrap;
  }
  .section-title strong { font-weight: 600; }
  .section-rule { height: 1px; background: var(--rule); }

  .body-copy { font-size: 5.5px; line-height: 1.42; color: var(--ink-soft); text-align: justify; }
  .body-copy p + p { margin-top: 6px; }
  .body-copy--bold { color: var(--ink); font-weight: 600; }

  .photo { display: block; }
  .hatch-block { background: linear-gradient(135deg, var(--tint-light), var(--tint-mid)); }
  .grey-shape { background: linear-gradient(180deg, #b8b8b8, #9c9c9c); }

  .contact { font-size: 6.6px; line-height: 1.35; color: var(--ink); }
  .contact .company { font-weight: 600; font-size: 7.4px; margin-bottom: 10px; }
  .contact .office { padding-left: 11px; margin-bottom: 10px; }
  .contact .line { position: relative; }
  .contact .line svg { position: absolute; left: -11px; top: 1px; width: 6px; height: 6px; }

  .wordmark { font-weight: 600; color: var(--ink); letter-spacing: 1px; line-height: 1; }
  .slogan {
    font-family: "Roboto Slab", serif;
    font-size: 12.5px;
    letter-spacing: -0.5px;
    color: var(--ink);
    white-space: nowrap;
  }

  .founders-tab {
    height: 12px;
    background: var(--black);
    color: #ffffff;
    font-size: 7.5px;
    font-weight: 500;
    line-height: 12px;
    padding-left: 9px;
    clip-path: polygon(0 0, 90% 0, 100% 100%, 0 100%);
  }
  .founders-rule { height: 1px; background: var(--rule); }
  .bio { font-size: 4.9px; line-height: 1.42; color: var(--ink-soft); text-align: justify; }

  .pocket {
    background: linear-gradient(180deg, #b9cde0 0%, #c5ccc6 22%, #8f9a74 38%, #8a7b68 60%, #6b6258 82%, #7d776f 100%);
    clip-path: polygon(14% 0, 100% 0, 100% 100%, 0 100%, 9% 16%);
  }
  .bottom-edge { height: 2px; background: var(--black); }
</style>
</head>
<body>

<!-- OUTER SPREAD -->
<section class="spread spread--outer" aria-label="Pagine esterne">
  <div class="panel-tint panel-tint--dotted" style="left:0;width:326px;"></div>
  <div class="panel-tint panel-tint--dotted" style="left:326px;width:326px;"></div>
  <div class="panel-tint panel-tint--cover" style="left:652px;width:325px;"></div>
  <div class="fold" style="left:326px;"></div>
  <div class="fold" style="left:652px;"></div>

  <!-- Our company -->
  <h2 class="section-title" style="left:34px;top:33px;">OUR <strong>COMPANY</strong></h2>
  <div class="section-rule" style="left:34px;top:53px;width:258px;"></div>
  <div class="body-copy" style="left:34px;top:64px;width:258px;">
    <p>TIRO Engineering S.r.l. offre servizi di consulenza tecnica, contrattuale e strategica ai principali attori nei settori delle scienze geologiche, dell’ingegneria geotecnica e dell’ingegneria idraulica. Lavoriamo per mitigare il rischio e ridurre l’incertezza, con flessibilità nella ricerca della soluzione ottimale contribuendo ad aumentare la redditività del progetto.</p>
    <p>TIRO Engineering S.r.l. è una società indipendente che nasce nel luglio 2020 dall’associazione di un gruppo di professionisti che hanno messo a fattor comune la reciproca esperienza maturata in oltre trent’anni di attività come progettisti e consulenti nel settore delle grandi opere di ingegneria civile lavorando come Direttori Tecnici di Main Engineering Companies and as Freelancers.</p>
    <p>TIRO Engineering S.r.l. vuole unire l’esperienza dei Fondatori e delle figure chiave con l’entusiasmo di chi intraprende una nuova attività, per dare vita ad una nuova realtà che si pone come obbiettivo principale il design of infrastructures that are safe, sustainable and economic.</p>
    <p>Each of our projects represents a long term commitment, we believe in providing safe, reliable, sustainable and innovative solutions. This is and will be our distinctive characteristic.</p>
  </div>
  <div class="hatch-block" style="left:130px;top:277px;width:162px;height:164px;"></div>
  <div class="photo" role="img" aria-label="Foto di cantiere urbano: scavo di fondazione con armature e edifici sullo sfondo" style="left:34px;top:214px;width:188px;height:206px;background:linear-gradient(180deg,#a9c6e2 0%,#c2b6a6 14%,#9d8474 24%,#a8a49c 38%,#b3aea6 55%,#9b958d 75%,#8a847c 100%);"></div>

  <!-- Our offices -->
  <div class="hatch-block" style="left:425px;top:37px;width:163px;height:162px;"></div>
  <div class="grey-shape" style="left:502px;top:190px;width:43px;height:170px;border-radius:43px 0 0 0;"></div>
  <h2 class="section-title" style="left:359px;top:269px;">OUR <strong>OFFICES</strong></h2>
  <div class="section-rule" style="left:359px;top:285px;width:144px;"></div>
  <div class="contact" style="left:359px;top:291px;width:150px;">
    <div class="company">TIRO Engineering S.r.l.</div>
    <div class="office">
      <div>Milano</div>
      <div class="line"><svg viewBox="0 0 10 10"><path d="M5 1a3 3 0 0 1 3 3c0 2-3 5-3 5S2 6 2 4a3 3 0 0 1 3-3z" fill="none" stroke="#2b2b2b" stroke-width="1"/></svg>Via Ortensi, 14</div>
      <div>20121 Milano - IT</div>
      <div class="line"><svg viewBox="0 0 10 10"><circle cx="5" cy="5" r="4" fill="none" stroke="#2b2b2b" stroke-width="1"/><path d="M3.5 3.5l1 1-0.5 0.8 1.2 1.2 0.8-0.5 1 1" fill="none" stroke="#2b2b2b" stroke-width="0.8"/></svg>+39 02 5550 1019</div>
      <div class="line"><svg viewBox="0 0 10 10"><rect x="1" y="2.5" width="8" height="5" fill="none" stroke="#2b2b2b" stroke-width="0.9"/><path d="M1 2.5l4 3 4-3" fill="none" stroke="#2b2b2b" stroke-width="0.9"/></svg>info@tiroengineering.org</div>
    </div>
    <div class="office">
      <div>Arco TN</div>
      <div class="line"><svg viewBox="0 0 10 10"><path d="M5 1a3 3 0 0 1 3 3c0 2-3 5-3 5S2 6 2 4a3 3 0 0 1 3-3z" fill="none" stroke="#2b2b2b" stroke-width="1"/></svg>Via dei Larici, 9</div>
      <div>38062 Arco TN - IT</div>
      <div class="line"><svg viewBox="0 0 10 10"><circle cx="5" cy="5" r="4" fill="none" stroke="#2b2b2b" stroke-width="1"/><path d="M3.5 3.5l1 1-0.5 0.8 1.2 1.2 0.8-0.5 1 1" fill="none" stroke="#2b2b2b" stroke-width="0.8"/></svg>+39 02 5550 1019</div>
      <div class="line"><svg viewBox="0 0 10 10"><rect x="1" y="2.5" width="8" height="5" fill="none" stroke="#2b2b2b" stroke-width="0.9"/><path d="M1 2.5l4 3 4-3" fill="none" stroke="#2b2b2b" stroke-width="0.9"/></svg>info@tiroengineering.org</div>
    </div>
    <div class="office">
      <div class="line"><svg viewBox="0 0 10 10"><circle cx="5" cy="5" r="4" fill="none" stroke="#2b2b2b" stroke-width="0.9"/><ellipse cx="5" cy="5" rx="1.8" ry="4" fill="none" stroke="#2b2b2b" stroke-width="0.7"/><path d="M1 5h8" stroke="#2b2b2b" stroke-width="0.7"/></svg>www.tiroengineering.org</div>
    </div>
  </div>
  <div class="wordmark" style="left:547px;top:410px;font-size:19px;">tiro</div>

  <!-- Cover -->
  <div class="wordmark" style="left:751px;top:34px;font-size:38px;">tiro</div>
  <div class="photo" role="img" aria-label="Galleria sotterranea in costruzione con due fornici illuminati, in toni blu e viola" style="left:545px;top:102px;width:265px;height:257px;background:linear-gradient(165deg,#7a86b8 0%,#5d6199 25%,#3f3f77 50%,#4a3d6e 72%,#272545 100%);"></div>
  <div class="photo" role="img" aria-label="Vista aerea di un cantiere con gru e materiali" style="left:813px;top:102px;width:159px;height:142px;background:linear-gradient(150deg,#b9b6b0 0%,#a08c7c 30%,#8d8b88 55%,#7e7167 80%,#a5a19a 100%);"></div>
  <div class="photo" role="img" aria-label="Vista aerea di un cantiere in zona boschiva con capannone" style="left:813px;top:248px;width:159px;height:111px;background:linear-gradient(150deg,#4f7540 0%,#a2a39e 35%,#b7b3ad 50%,#8c8070 70%,#4c7a3c 100%);"></div>
  <div class="slogan" style="left:685px;top:401px;">TIRO ENGINEERING, RELIABLE SOLUTIONS</div>
</section>

<!-- INNER SPREAD -->
<section class="spread spread--inner" aria-label="Pagine interne">
  <div class="panel-tint panel-tint--inner-left" style="left:0;width:326px;"></div>
  <div class="panel-tint panel-tint--inner-mid" style="left:326px;width:326px;"></div>
  <div class="panel-tint panel-tint--inner-right" style="left:652px;width:325px;"></div>
  <div class="fold" style="left:326px;"></div>
  <div class="fold" style="left:652px;"></div>

  <!-- Our services -->
  <h2 class="section-title" style="left:33px;top:26px;">OUR <strong>SERVICES</strong></h2>
  <div class="section-rule" style="left:33px;top:44px;width:259px;"></div>
  <div class="body-copy" style="left:33px;top:52px;width:259px;">
    <p>Progettazione e consulenza specialistica nel campo della geologia, dell’ingegneria geotecnica, delle opere sotterranee e dell’ingegneria idtraulica.</p>
    <p>Aiutiamo i nostri clienti a risolvere problemi di natura progettuale, contrattuale e costruttiva che possono nascere nell’intera vita del progetto portando la nostra esperienza all’interno delle loro organizzazioni, migliorando la qualità dei loro servizi di ingegneria, ottimizzando i loro progetti, proponendo nuove idee e soluzioni, rafforzando i loro approcci ......</p>
    <p>TIRO Engineering è in grado di fornire la propria assistenza nell’intero iter procedurale, dalla fase di indagine preliminare e di analisi di fattibilità fino alla progettazione costruttiva e all’assistenza tecnica in fase realizzativa.</p>
  </div>
  <div class="photo" role="img" aria-label="Fronte di scavo di una galleria con centine e roccia" style="left:34px;top:137px;width:257px;height:115px;background:linear-gradient(180deg,#8c8a7c 0%,#a39a82 25%,#b39a6e 45%,#8e7653 65%,#9a8f7a 85%,#7c7364 100%);"></div>
  <div class="body-copy body-copy--bold" style="left:34px;top:262px;width:257px;">La specializzazione e l’esperienza accumulate nelle discipline della geologia, dell’ingegneria geotecnica e del sottosuolo e dell’idraulica ci permette di massimizzare la nostra efficacia quando sia necessario:</div>
  <div class="hatch-block" style="left:22px;top:330px;width:48px;height:48px;"></div>
  <div class="photo" role="img" aria-label="Pozzo di scavo con strutture in calcestruzzo" style="left:34px;top:292px;width:91px;height:75px;background:linear-gradient(160deg,#a49e94 0%,#7d766c 40%,#958f86 70%,#b1aca4 100%);"></div>
  <div class="body-copy" style="left:144px;top:296px;width:148px;">
    <p>far fronte a situazioni di emergenza anche su progetti in fase di sviluppo avanzato garantendo l’immediata focalizzazione delle problematiche di progetto e garantendo il risultato finale atteso (in termini di qualità, tempistiche e costi…)</p>
    <p>fornire “second opinion” di elevato valore tecnico ed amministrativo in occasione di problematiche progettuali e costruttive e dispute legali</p>
  </div>
  <div class="hatch-block" style="left:243px;top:405px;width:56px;height:46px;"></div>
  <div class="photo" role="img" aria-label="Cantiere in centro città con opere di fondazione" style="left:199px;top:368px;width:92px;height:75px;background:linear-gradient(170deg,#b5aca2 0%,#8b6f62 25%,#9a9187 55%,#7f776d 100%);"></div>
  <div class="body-copy" style="left:33px;top:384px;width:150px;">
    <p>analizzare in tempi brevi progetti svolti da terzi individuandone le “criticità”, verificandone la cantierabilità e la validità tecnico economica.</p>
    <p>ottimizzare i progetti redatti da terzi implementandone il contenuto e massimizzando l’efficacia economica degli investimenti.</p>
  </div>

  <!-- Expertise -->
  <h2 class="section-title" style="left:358px;top:26px;">OUR <strong>EXPERTISE AND EXPERIENCE</strong></h2>
  <div class="section-rule" style="left:359px;top:44px;width:259px;"></div>
  <div class="body-copy" style="left:359px;top:54px;width:258px;">
    <p>La società nasce dall’associazione di un gruppo di professionisti, con indiscusse competenze ed affidabilità, con esperienza maturata in oltre trent’anni di attività come progettisti e consulenti nel settore delle grandi opere di ingegneria civile; geologia, ingegneria geotecnica ed idraulica ed opere sotterranee sono il “core” delle loro competenze ....</p>
  </div>
  <div class="founders-tab" style="left:359px;top:93px;width:142px;">I SOCI FONDATORI SONO:</div>
  <div class="founders-rule" style="left:359px;top:104px;width:261px;"></div>
  <div class="bio" style="left:359px;top:109px;width:261px;">Luca. Già Direttore Tecnico e Socio di KORA Srl, nel periodo di sua permanenza fino al dicembre 2018, ha per essa firmato tutti i progetti nel campo delle opere sotterranee e la maggior parte di quelli di ingegneria geotecnica. Da gennaio 2019 è Direttore Tecnico di VELTA. Può vantare più di 150 gallerie naturali, e numerosi progetti ed assistenze tecniche nel campo delle strutture geotecniche, delle sistemazioni idrogeologiche e dei versanti e delle opere di protezione ambientale. Negli ultimi dieci anni è stato responsabile di attività di assistenza tecnica, per imprese di costruzione, di opere il cui valore supera i 440 Mio EUR e di servizi di progettazione definitiva ed esecutiva per opere il cui valore supera i 1.400 Mio EUR. Ha svolto attività di verifica e validazione, in Italia ed all’estero, di numerosi progetti il cui valore complessivo supera i 3.400 Mio EUR.</div>
  <div class="photo" role="img" aria-label="Spazio per la foto del team" style="left:361px;top:178px;width:257px;height:98px;background:linear-gradient(180deg,#eeeae2 0%,#e0d2c4 30%,#c7a99a 55%,#8f9fba 80%,#b9b4c4 100%);"></div>
  <div class="bio" style="left:359px;top:287px;width:261px;">Marco 30 anni di esperienza professionale. Coinvolto in più di 150 gallerie naturali con lunghezza complessiva superiore a 360 km. Numerosi progetti ed attività di assistenza tecnica nel campo delle strutture, delle sistemazioni idrogeologiche e dei versanti e delle opere di protezione ambientale. Negli ultimi dieci anni responsabile di attività di assistenza tecnica in corso d’opera, per imprese di costruzione, di opere il cui valore supera i 440 Mio EUR e di servizi di progettazione definitiva o esecutiva per opere il cui valore supera i 1.400 Mio EUR. Ha svolto attività di verifica ai fini della validazione, in Italia ed all’estero, di numerosi progetti il cui valore complessivo supera i 3.400 Mio EUR.</div>
  <div class="bio" style="left:359px;top:341px;width:261px;">Giulia 30 anni di esperienza professionale. Coinvolta in più di 150 gallerie naturali con lunghezza complessiva superiore a 360 km. Numerosi progetti ed attività di assistenza tecnica nel campo delle strutture, delle sistemazioni idrogeologiche e dei versanti e delle opere di protezione ambientale. Negli ultimi dieci anni responsabile di attività di assistenza tecnica in corso d’opera, per imprese di costruzione, di opere il cui valore supera i 440 Mio EUR e di servizi di progettazione definitiva o esecutiva per opere il cui valore supera i 1.400 Mio EUR. Ha svolto attività di verifica ai fini della validazione, in Italia ed all’estero, di numerosi progetti il cui valore complessivo supera i 3.400 Mio EUR.</div>
  <div class="bio" style="left:359px;top:395px;width:261px;">Chiara 30 anni di esperienza professionale. Coinvolta in più di 150 gallerie naturali con lunghezza complessiva superiore a 360 km. Numerosi progetti ed attività di assistenza tecnica nel campo delle strutture, delle sistemazioni idrogeologiche e dei versanti e delle opere di protezione ambientale. Negli ultimi dieci anni responsabile di attività di assistenza tecnica in corso d’opera, per imprese di costruzione, di opere il cui valore supera i 440 Mio EUR e di servizi di progettazione definitiva o esecutiva per opere il cui valore supera i 1.400 Mio EUR. Ha svolto attività di verifica ai fini della validazione, in Italia ed all’estero, di numerosi progetti il cui valore complessivo supera i 3.400 Mio EUR.</div>

  <!-- Pocket page -->
  <div class="photo" role="img" aria-label="Sollevamento di una fresa TBM con gru cingolata" style="left:681px;top:35px;width:142px;height:140px;background:linear-gradient(170deg,#3f7fc2 0%,#6a9fd2 30%,#b4524c 50%,#8a8f96 70%,#3b63a8 85%,#a59d90 100%);"></div>
  <div class="photo" role="img" aria-label="Versante collinare gradonato con opere di sostegno" style="left:835px;top:35px;width:113px;height:140px;background:linear-gradient(180deg,#426f36 0%,#5f7f4a 30%,#9b9890 55%,#b4b0a8 80%,#9f9b94 100%);"></div>
  <div class="photo" role="img" aria-label="Imbocchi di due gallerie in un versante di scavo" style="left:681px;top:185px;width:267px;height:141px;background:linear-gradient(180deg,#c5cdd6 0%,#b8b3a1 25%,#8f8a73 45%,#5f5c52 65%,#8a8476 85%,#a39e92 100%);"></div>
  <div class="pocket" role="img" aria-label="Tasca incollata con foto di cantiere e escavatore" style="left:666px;top:348px;width:311px;height:112px;"></div>
  <div class="wordmark" style="left:770px;top:395px;font-size:52px;color:var(--black);">tiro</div>

  <div class="bottom-edge" style="left:0;top:458px;width:666px;"></div>
</section>

</body>
</html>
```